Rapid Pulse Tiny Track Karts

We are looking for a full web site for our race car category that allows us to edit and update some of the content. We would like the site to feel modern and attractive with the following features: 1. Event calender (with the ability for us to update) 2. Social media/ clip wave links 3. photo gallery (with the ability for us to update) 4. Member area with log in access (controlled access) - this area to include access to category regulations for up to 5 types of cars separately 5. Championship ladder for up to 5 different groups 6. sponsor page and sponsors scrolling across bottom of all pages. Please find attached our logo to be used and for reference on color/ style 7. page to show merchandise but no need for a store.

Industry/Entity Type

Motor racing category

Coding

Coded - Design and coding required

Number of Pages Required

5+ page

Colors
0054AA
0677BA
7BADD7
CADEEF
E8F1F8
FFF300
FFF600
FEFA6F
FFFEC7
FFFEE8
EB3D1F
EC4F4E
F09395
F8D3D4
FCEDEE

Requirements
Must have
• Ability to update calender/photo gallery/championship ladder including points/ notice board - Members section

```html
<!DOCTYPE html>
<html lang="en">
<head>
<meta charset="utf-8">
<title>Rapid Pulse Tiny Track Karts</title>
<link href="https://fonts.googleapis.com/css2?family=Barlow:wght@400;500;600;700&family=Bungee&display=swap" rel="stylesheet">
<style>
:root{
  --black:#000;
  --ink:#222;
  --muted:#777;
  --yellow:#fbd02a;
  --blue:#0a5ad6;
  --link:#1f55c9;
  --red:#ee1c1c;
  --grey-band:#f2f2f2;
  --footer:#1f1f1f;
  --white:#fff;
}
*{margin:0;padding:0;box-sizing:border-box}
html,body{width:1200px;height:4080px;overflow:hidden}
body{position:relative;font-family:"Barlow",sans-serif;color:var(--ink);background:var(--white)}
.abs{position:absolute}
.section-title{position:absolute;left:0;width:1200px;text-align:center;font-family:"Bungee",sans-serif;font-size:36px;color:#1a1a1a;letter-spacing:-1px}

/* header */
.site-header{position:absolute;left:0;top:0;width:1200px;height:107px;background:var(--black)}
.brand{position:absolute;left:112px;top:22px;width:174px;height:62px;border:2px solid var(--white);border-radius:6px;display:flex;align-items:center;gap:8px;padding:0 10px;color:var(--white);font-weight:700;font-size:14px;line-height:1.1;text-transform:uppercase}
.brand-mark{width:14px;height:14px;background:var(--red);flex:none}
.main-nav{position:absolute;left:397px;top:45px;display:flex;gap:26px;font-weight:700;font-size:13px;color:var(--white)}
.main-nav .active{color:var(--yellow);position:relative}
.main-nav .active::after{content:"";position:absolute;left:0;right:0;top:52px;height:4px;background:var(--yellow)}
.search{position:absolute;left:782px;top:32px;width:231px;height:44px;border:1px solid #888;border-radius:6px;color:#ddd;font-size:12px;padding:14px 17px}
.search svg{position:absolute;right:14px;top:15px}
.login{position:absolute;left:1066px;top:32px;width:134px;height:44px;background:var(--yellow);border-radius:6px 0 0 6px;font-weight:700;font-size:13px;color:#222;padding:14px 26px}

/* hero */
.hero{position:absolute;left:0;top:107px;width:1200px;height:643px;background:
  radial-gradient(ellipse 260px 160px at 600px 150px,rgba(255,214,120,.85),rgba(255,180,60,0) 100%),
  radial-gradient(ellipse 420px 300px at 600px 200px,rgba(200,140,50,.8),rgba(120,80,30,0) 100%),
  linear-gradient(100deg,rgba(0,0,0,0) 0%,rgba(0,0,0,0) 100%),
  linear-gradient(180deg,#3a2a16 0%,#5a4020 28%,#2a1e12 48%,#1a1510 72%,#2e2820 84%,#14110e 100%)}
.hero::before{content:"";position:absolute;left:0;top:90px;width:1200px;height:330px;background:
  linear-gradient(160deg,rgba(10,8,6,.85) 0%,rgba(10,8,6,.6) 18%,rgba(10,8,6,0) 35%),
  linear-gradient(200deg,rgba(10,8,6,.85) 0%,rgba(10,8,6,.6) 18%,rgba(10,8,6,0) 35%)}
.hero::after{content:"";position:absolute;left:330px;top:130px;width:540px;height:513px;background:radial-gradient(ellipse 200px 330px at 270px 400px,rgba(8,6,4,.85),rgba(8,6,4,0) 100%)}
.hero h1{position:absolute;z-index:1;left:0;top:240px;width:1200px;text-align:center;font-family:"Bungee",sans-serif;color:var(--white);font-size:36px;line-height:52px;font-weight:400;letter-spacing:-1px}
.btn-start{position:absolute;z-index:1;left:536px;top:357px;width:128px;height:40px;background:var(--yellow);border-radius:6px;text-align:center;line-height:40px;font-weight:700;font-size:13px;color:#222}
.dots{position:absolute;z-index:1;left:565px;top:535px;display:flex;gap:7px}
.dots span{width:12px;height:12px;border-radius:50%;border:2px solid var(--white)}
.dots span:first-child{background:var(--white)}

/* events */
.event-card{position:absolute;top:928px;width:300px;height:406px;background:var(--blue);border-radius:4px;color:var(--white)}
.event-card .photo{position:absolute;left:1px;top:24px;width:277px;height:208px;border-radius:0 0 6px 6px}
.event-card h3{position:absolute;left:32px;top:248px;font-size:20px;font-weight:700}
.event-card p{position:absolute;left:33px;top:290px;width:240px;font-size:13px;line-height:21.5px}
.side-arrow{position:absolute;top:1096px;width:68px;height:68px;border-radius:50%;background:var(--blue)}

/* video */
.video-band{position:absolute;left:0;top:1437px;width:1200px;height:398px;background:
  radial-gradient(ellipse 170px 90px at 690px 250px,rgba(230,130,30,.95),rgba(230,130,30,0) 100%),
  radial-gradient(ellipse 140px 80px at 1020px 230px,rgba(200,30,40,.95),rgba(200,30,40,0) 100%),
  radial-gradient(ellipse 160px 70px at 350px 220px,rgba(150,60,40,.7),rgba(150,60,40,0) 100%),
  radial-gradient(ellipse 600px 120px at 600px 130px,rgba(240,160,80,.55),rgba(240,160,80,0) 100%),
  linear-gradient(180deg,#16161a 0%,#2c2620 25%,#6b4a2a 45%,#3a2c22 72%,#17151a 100%)}
.play{position:absolute;left:568px;top:1614px;width:62px;height:44px;background:var(--red);border-radius:12px}

/* gallery */
.gallery{position:absolute;left:0;top:1835px;width:1200px;height:725px;background:var(--grey-band)}
.tile{position:absolute;border-radius:3px}

/* ladder */
.rank{position:absolute;width:302px;text-align:center}
.rank .pos{position:absolute;left:120px;width:61px;height:54px;background:var(--red);color:var(--white);font-weight:700;font-size:21px;line-height:54px}
.rank .photo{position:absolute;left:0;width:302px;height:198px}
.rank h3{position:absolute;left:0;width:100%;font-size:20px;font-weight:600;color:#222}
.rank p{position:absolute;left:15px;width:272px;font-size:13.5px;line-height:21.5px;color:var(--muted)}
.rank a{position:absolute;left:0;width:100%;font-size:13px;font-weight:700;color:var(--link);text-decoration:underline}
.small-arrow{position:absolute;width:36px;height:36px;border-radius:50%;background:#ddd}

/* sponsors */
.sponsor{position:absolute;top:3430px;width:164px;height:164px;border-radius:50%;background:var(--white);box-shadow:0 4px 16px rgba(0,0,0,.12)}
.sponsor span{position:absolute;left:44px;top:44px;width:76px;height:76px;border-radius:50%}

/* footer */
.site-footer{position:absolute;left:0;top:3698px;width:1200px;height:382px;background:var(--footer);color:var(--white)}
.f-col{position:absolute;top:80px}
.f-col h4{font-size:21px;font-weight:500;line-height:26px;margin-bottom:18px}
.f-col li{list-style:none;display:flex;align-items:flex-start;gap:12px;font-size:14px;line-height:21.5px}
.f-col li .ic{width:22px;flex:none;color:var(--red);font-size:13px;padding-top:3px}
.divider{position:absolute;top:82px;width:1px;height:160px;background:#444}
.copyright{position:absolute;left:0;top:311px;width:1200px;text-align:center;font-size:13.5px}
</style>
</head>
<body>

<header class="site-header">
  <div class="brand"><span class="brand-mark"></span>Rapid Pulse Tiny Track Karts</div>
  <nav class="main-nav">
    <span class="active">HOME</span><span>ABOUT</span><span>SERVICES</span><span>BLOG</span><span>CONTACT</span>
  </nav>
  <div class="search">Search
    <svg width="12" height="12" viewBox="0 0 12 12"><circle cx="5" cy="5" r="3.6" fill="none" stroke="#fff" stroke-width="1.8"/><line x1="7.7" y1="7.7" x2="11" y2="11" stroke="#fff" stroke-width="2"/></svg>
  </div>
  <div class="login">&#9679; LOGIN</div>
</header>

<section class="hero" role="img" aria-label="Driver with raised arms silhouetted against a golden sunset over race track grandstands">
  <h1>Rapid Pulse<br>Tiny Track Karts</h1>
  <div class="btn-start">GET STARTED</div>
  <div class="dots"><span></span><span></span><span></span><span></span></div>
</section>

<h2 class="section-title" style="top:845px">Event Calendar</h2>
<div class="side-arrow" style="left:-34px"><svg class="abs" style="left:40px;top:27px" width="10" height="14" viewBox="0 0 10 14"><path d="M8 2 3 7l5 5" fill="none" stroke="#fff" stroke-width="2"/></svg></div>
<div class="side-arrow" style="left:1166px"><svg class="abs" style="left:18px;top:27px" width="10" height="14" viewBox="0 0 10 14"><path d="M2 2l5 5-5 5" fill="none" stroke="#fff" stroke-width="2"/></svg></div>

<article class="event-card" style="left:111px">
  <div class="photo" role="img" aria-label="Red race car in pit lane with crew" style="background:radial-gradient(ellipse 110px 60px at 150px 130px,rgba(200,30,30,.95),rgba(200,30,30,0) 100%),radial-gradient(ellipse 60px 90px at 250px 80px,rgba(170,20,20,.8),rgba(170,20,20,0) 100%),linear-gradient(180deg,#6c7078 0%,#3c3e44 45%,#2a2b30 100%)"></div>
  <h3>Lorem ipsum dolor sit</h3>
  <p>Lorem ipsum dolor sit amet, consec tetur adipiscing elit, sed do eiusmod tempor incididunt ut labore et dolore magna aliqua.</p>
</article>
<article class="event-card" style="left:451px">
  <div class="photo" role="img" aria-label="Red formula car racing on a track" style="background:radial-gradient(ellipse 100px 55px at 140px 110px,rgba(210,40,50,.95),rgba(210,40,50,0) 100%),linear-gradient(180deg,#9fb4cc 0%,#d8dde2 30%,#b23a3a 42%,#8f8f95 60%,#4a4a50 100%)"></div>
  <h3>Lorem ipsum dolor sit</h3>
  <p>Lorem ipsum dolor sit amet, consec tetur adipiscing elit, sed do eiusmod tempor incididunt ut labore et dolore magna aliqua.</p>
</article>
<article class="event-card" style="left:789px">
  <div class="photo" role="img" aria-label="Yellow formula car with driver in helmet" style="background:radial-gradient(ellipse 120px 60px at 140px 140px,rgba(230,180,30,.95),rgba(230,180,30,0) 100%),radial-gradient(ellipse 30px 30px at 140px 70px,rgba(200,40,40,.8),rgba(200,40,40,0) 100%),linear-gradient(180deg,#5a5e66 0%,#3a3c42 40%,#1e1f23 100%)"></div>
  <h3>Lorem ipsum dolor sit</h3>
  <p>Lorem ipsum dolor sit amet, consec tetur adipiscing elit, sed do eiusmod tempor incididunt ut labore et dolore magna aliqua.</p>
</article>

<section class="video-band" role="img" aria-label="Sports cars racing at night under stadium lights, clip wave video"></section>
<div class="play"><svg class="abs" style="left:23px;top:13px" width="18" height="18" viewBox="0 0 18 18"><path d="M2 1l15 8-15 8z" fill="#fff"/></svg></div>

<section class="gallery">
  <h2 class="section-title" style="top:90px">Gallery</h2>
  <div class="tile" role="img" aria-label="Red formula car leading a race" style="left:111px;top:162px;width:489px;height:435px;background:radial-gradient(ellipse 200px 110px at 270px 250px,rgba(200,30,25,.95),rgba(200,30,25,0) 100%),radial-gradient(ellipse 140px 40px at 300px 90px,rgba(190,60,50,.6),rgba(190,60,50,0) 100%),linear-gradient(180deg,#6a786e 0%,#4a554e 35%,#2e3230 70%,#1e2020 100%)"></div>
  <div class="tile" role="img" aria-label="Red formula car at speed" style="left:618px;top:162px;width:225px;height:206px;background:radial-gradient(ellipse 90px 50px at 120px 110px,rgba(200,20,30,.95),rgba(200,20,30,0) 100%),linear-gradient(160deg,#c83038 0%,#ead8d8 40%,#8a8a90 70%,#2e2e32 100%)"></div>
  <div class="tile" role="img" aria-label="Driver in orange suit in cockpit" style="left:862px;top:162px;width:227px;height:206px;background:radial-gradient(ellipse 90px 70px at 115px 120px,rgba(220,120,30,.9),rgba(220,120,30,0) 100%),radial-gradient(ellipse 120px 40px at 115px 20px,rgba(210,220,235,.6),rgba(210,220,235,0) 100%),linear-gradient(180deg,#50545c 0%,#2e3036 55%,#18191c 100%)"></div>
  <div class="tile" role="img" aria-label="Formula car on a covered straight" style="left:618px;top:389px;width:225px;height:206px;background:radial-gradient(ellipse 60px 30px at 110px 130px,rgba(40,60,140,.9),rgba(40,60,140,0) 100%),linear-gradient(180deg,#30343a 0%,#a8b0ba 30%,#6a707a 55%,#2a2d33 100%)"></div>
  <div class="tile" role="img" aria-label="Red sports car wheel at sunset" style="left:862px;top:389px;width:227px;height:206px;background:radial-gradient(ellipse 90px 110px at 210px 110px,rgba(200,50,40,.95),rgba(200,50,40,0) 100%),linear-gradient(180deg,#e8c890 0%,#c8905a 40%,#6a4a38 70%,#2a2220 100%)"></div>
</section>

<h2 class="section-title" style="top:2660px">Championship Ladder</h2>
<div class="small-arrow" style="left:37px;top:2972px"><svg class="abs" style="left:13px;top:12px" width="8" height="12" viewBox="0 0 8 12"><path d="M6 1 1 6l5 5" fill="none" stroke="#333" stroke-width="1.8"/></svg></div>
<div class="small-arrow" style="left:1127px;top:2972px"><svg class="abs" style="left:15px;top:12px" width="8" height="12" viewBox="0 0 8 12"><path d="M2 1l5 5-5 5" fill="none" stroke="#333" stroke-width="1.8"/></svg></div>

<div class="rank" style="left:111px;top:2826px">
  <div class="pos" style="top:0">02</div>
  <div class="photo" role="img" aria-label="White formula car on track under dramatic sky" style="top:54px;background:radial-gradient(ellipse 80px 40px at 150px 120px,rgba(230,230,235,.85),rgba(230,230,235,0) 100%),radial-gradient(ellipse 120px 40px at 80px 70px,rgba(240,200,140,.8),rgba(240,200,140,0) 100%),linear-gradient(180deg,#3c4450 0%,#6a6e72 40%,#4a4e56 60%,#1c1e22 100%)"></div>
  <h3 style="top:270px">Lorem ipsum dolor</h3>
  <p style="top:308px">Lorem ipsum dolor sit amet, consectetur adipiscing elit, sed do eiusmod tempor incididunt ut labore et dolo</p>
  <a style="top:386px">READ MORE</a>
</div>
<div class="rank" style="left:449px;top:2766px">
  <div class="pos" style="top:0">01</div>
  <div class="photo" role="img" aria-label="Driver in red suit standing beside a red formula car" style="top:54px;background:radial-gradient(ellipse 30px 80px at 151px 90px,rgba(200,30,30,.95),rgba(200,30,30,0) 100%),radial-gradient(ellipse 110px 35px at 151px 150px,rgba(150,20,20,.85),rgba(150,20,20,0) 100%),linear-gradient(180deg,#2a2c32 0%,#1a1b1f 100%)"></div>
  <h3 style="top:270px">Lorem ipsum dolor</h3>
  <p style="top:308px">Lorem ipsum dolor sit amet, consectetur adipiscing elit, sed do eiusmod tempor incididunt ut labore et dolo</p>
  <a style="top:386px">READ MORE</a>
</div>
<div class="rank" style="left:787px;top:2826px">
  <div class="pos" style="top:0">03</div>
  <div class="photo" role="img" aria-label="Dark formula car on track at sunset" style="top:54px;background:radial-gradient(ellipse 110px 40px at 150px 120px,rgba(20,20,24,.9),rgba(20,20,24,0) 100%),linear-gradient(180deg,#2a1a10 0%,#d28a30 30%,#8a5a30 50%,#2e3038 75%,#1a1b20 100%)"></div>
  <h3 style="top:270px">Lorem ipsum dolor</h3>
  <p style="top:308px">Lorem ipsum dolor sit amet, consectetur adipiscing elit, sed do eiusmod tempor incididunt ut labore et dolo</p>
  <a style="top:386px">READ MORE</a>
</div>

<h2 class="section-title" style="top:3332px">Sponsors</h2>
<div class="small-arrow" style="left:37px;top:3494px"><svg class="abs" style="left:13px;top:12px" width="8" height="12" viewBox="0 0 8 12"><path d="M6 1 1 6l5 5" fill="none" stroke="#333" stroke-width="1.8"/></svg></div>
<div class="small-arrow" style="left:1127px;top:3494px"><svg class="abs" style="left:15px;top:12px" width="8" height="12" viewBox="0 0 8 12"><path d="M2 1l5 5-5 5" fill="none" stroke="#333" stroke-width="1.8"/></svg></div>
<div class="sponsor" style="left:110px" role="img" aria-label="Sponsor badge"><span style="background:#2a8fd0"></span></div>
<div class="sponsor" style="left:314px" role="img" aria-label="Sponsor badge"><span style="background:#8a4fd6"></span></div>
<div class="sponsor" style="left:519px" role="img" aria-label="Sponsor badge"><span style="background:#1c9ad6"></span></div>
<div class="sponsor" style="left:723px" role="img" aria-label="Sponsor badge"><span style="background:#8cc63f"></span></div>
<div class="sponsor" style="left:927px" role="img" aria-label="Sponsor badge"><span style="background:#d9a441"></span></div>

<footer class="site-footer">
  <div class="f-col" style="left:109px;top:76px;width:240px">
    <h4>Rapid Pulse Tiny Track Karts</h4>
    <ul>
      <li><span class="ic"><svg width="10" height="13" viewBox="0 0 10 13"><path d="M5 0a5 5 0 0 1 5 5c0 3.5-5 8-5 8S0 8.5 0 5a5 5 0 0 1 5-5z" fill="#ee1c1c"/><circle cx="5" cy="5" r="1.8" fill="#1f1f1f"/></svg></span>123 Lorem ipsum dolor<br>sit amet</li>
      <li><span class="ic"><svg width="13" height="10" viewBox="0 0 13 10"><rect width="13" height="10" rx="1" fill="#ee1c1c"/><path d="M0 1l6.5 5L13 1" fill="none" stroke="#1f1f1f" stroke-width="1.2"/></svg></span>hello@rapidpulsekarts.test</li>
      <li><span class="ic"><svg width="12" height="12" viewBox="0 0 12 12"><path d="M2.5 0 5 3 3.5 4.5a8 8 0 0 0 4 4L9 7l3 2.5-1.5 2C5 12 0 7 .5 1.5z" fill="#ee1c1c"/></svg></span>555-018-2046</li>
    </ul>
  </div>
  <div class="divider" style="left:360px"></div>
  <div class="f-col" style="left:414px">
    <h4>Legal</h4>
    <ul><li><span class="ic">»</span>Terms</li><li><span class="ic">»</span>Privacy Policy</li><li><span class="ic">»</span>Cookie Policy</li><li><span class="ic">»</span>Verify Company</li></ul>
  </div>
  <div class="divider" style="left:626px"></div>
  <div class="f-col" style="left:700px">
    <h4>Support</h4>
    <ul><li><span class="ic">»</span>Support</li><li><span class="ic">»</span>FAQ</li><li><span class="ic">»</span>Contact us</li><li><span class="ic">»</span>Buy Track Tokens</li></ul>
  </div>
  <div class="divider" style="left:906px"></div>
  <div class="f-col" style="left:990px">
    <h4>Social</h4>
    <ul><li><span class="ic">●</span>Circlebook</li><li><span class="ic">●</span>Snapgrid</li><li><span class="ic">●</span>Workline</li></ul>
  </div>
  <p class="copyright">© Copyrights 2023 | All Rights Reserved | Privacy Policy</p>
</footer>

</body>
</html>
```